Business Card for Coastal Tundrabridge Advisory

We need a business card for Coastal Tundrabridge Advisory. The company website address is provided below. The company logo is attached. We provide specialized permafrost services to the mining, transportation, and oil & gas industries. The card should be prepared for:
Matthias Korhonen, PhD.
Coastal Tundrabridge Advisory
PO Box 418259
Quillwater, Alaska 99642
Direct: +1-907-555-0143
Email: mkorhonen@tundrabridgeadvisory.example
Website: www.coastaltundrabridgeadvisory.example

```html
<!DOCTYPE html>
<html lang="en">
<head>
<meta charset="utf-8">
<title>Coastal Tundrabridge Advisory — Business Card</title>
<link rel="stylesheet" href="https://fonts.googleapis.com/css2?family=Montserrat:wght@400;500;600;700&display=swap">
<style>
  :root {
    --backdrop: #9a9a9a;
    --card: #ffffff;
    --ink: #111820;
  }
  * { margin: 0; padding: 0; box-sizing: border-box; }
  html, body { width: 1093px; height: 1200px; overflow: hidden; }
  body {
    background: var(--backdrop);
    position: relative;
    font-family: "Montserrat", sans-serif;
    color: var(--ink);
  }
  .card {
    position: absolute;
    left: 264px;
    width: 581px;
    background: var(--card);
    border-radius: 18px;
  }
  .card--front { top: 225px; height: 363px; }
  .card--back  { top: 616px; height: 366px; }

  .wordmark {
    position: absolute;
    text-align: center;
    font-weight: 600;
    text-transform: uppercase;
    line-height: 1.15;
    color: var(--ink);
  }
  .card--front .wordmark {
    left: 40px; width: 208px; top: 193px;
    font-size: 11.5px; letter-spacing: 0.06em;
  }
  .card--back .wordmark {
    left: 0; width: 100%; top: 150px;
    font-size: 27px; letter-spacing: 0.06em;
  }
  .wordmark .wordmark__line2 { letter-spacing: 0.35em; }

  .divider {
    position: absolute;
    left: 243px; top: 121px;
    width: 1px; height: 167px;
    background: var(--ink);
  }
  .details { position: absolute; left: 252px; top: 121px; }
  .details__name { font-size: 18.5px; font-weight: 700; line-height: 1.2; }
  .details__title { font-size: 12.5px; font-weight: 400; margin-top: 2px; }
  .details__address { font-size: 13px; line-height: 16px; margin-top: 13px; margin-left: 2px; }
  .contact { list-style: none; margin-top: 17px; margin-left: 2px; }
  .contact__item {
    display: flex; align-items: center;
    font-size: 12.5px; height: 25px;
  }
  .contact__icon { width: 13px; height: 13px; margin-right: 10px; flex: none; fill: var(--ink); }
</style>
</head>
<body>
  <section class="card card--front" aria-label="Business card front">
    <div class="wordmark">Coastal Tundrabridge<br><span class="wordmark__line2">Advisory</span></div>
    <div class="divider"></div>
    <div class="details">
      <p class="details__name">Matthias Korhonen, PhD.</p>
      <p class="details__title">Managing Director</p>
      <p class="details__address">PO Box 418259<br>Quillwater, Alaska 99642</p>
      <ul class="contact">
        <li class="contact__item">
          <svg class="contact__icon" viewBox="0 0 24 24" aria-hidden="true"><path d="M6.6 10.8a15.1 15.1 0 0 0 6.6 6.6l2.2-2.2c.3-.3.7-.4 1-.2 1.1.4 2.3.6 3.6.6.6 0 1 .4 1 1V20c0 .6-.4 1-1 1A17 17 0 0 1 3 4c0-.6.4-1 1-1h3.5c.6 0 1 .4 1 1 0 1.3.2 2.5.6 3.6.1.3 0 .7-.2 1z"/></svg>
          +1-907-555-0143
        </li>
        <li class="contact__item">
          <svg class="contact__icon" viewBox="0 0 24 24" aria-hidden="true"><path d="M2 5h20v14H2z M2 5l10 7 10-7" fill="var(--ink)"/><path d="M3 6l9 6.3L21 6" fill="none" stroke="#fff" stroke-width="1.6"/></svg>
          mkorhonen@tundrabridgeadvisory.example
        </li>
        <li class="contact__item">
          <svg class="contact__icon" viewBox="0 0 24 24" aria-hidden="true"><circle cx="12" cy="12" r="10"/><path d="M7 6c2 1 2 3 4 3s1 3-1 4-1 4-3 3M15 4c0 2 2 2 3 4s-1 3 0 5 2 2 1 4" fill="none" stroke="#fff" stroke-width="1.5"/></svg>
          www.coastaltundrabridgeadvisory.example
        </li>
      </ul>
    </div>
  </section>

  <section class="card card--back" aria-label="Business card back">
    <div class="wordmark">Coastal Tundrabridge<br><span class="wordmark__line2">Advisory</span></div>
  </section>
</body>
</html>
```